Marwick Law Letterhead

We need a new letterhead design for a Law Firm. The address for the law firm is 1475 Calloway Street, Suite 210, Houston, Texas 77041. Phone Number: 832-361-9027; Fax Number: 832-614-7359. The logo is uploaded to the project.

```html
<!DOCTYPE html>
<html lang="en">
<head>
<meta charset="utf-8">
<title>Marwick Law Letterhead</title>
<link href="https://fonts.googleapis.com/css2?family=Mulish:wght@400;700&family=Roboto:wght@400&display=swap" rel="stylesheet">
<style>
  :root {
    --navy: #13244a;
    --navy-light: #1b3166;
    --red-dark: #7a1218;
    --red: #d21f26;
    --paper: #f0f0f0;
    --backdrop: #dcdcdc;
    --ink: #2a2a2a;
    --white: #ffffff;
    --placeholder: #e4e4e4;
  }
  html, body {
    margin: 0;
    padding: 0;
    width: 1069px;
    height: 1200px;
    overflow: hidden;
    background: var(--backdrop);
  }
  .letterhead {
    position: absolute;
    left: 124px;
    top: 21px;
    width: 1107px;
    height: 1564px;
    background: var(--paper);
    transform: scale(0.7407);
    transform-origin: top left;
    overflow: hidden;
    font-family: "Mulish", sans-serif;
    color: var(--ink);
  }
  .header-band {
    position: absolute;
    left: 0;
    top: 0;
    width: 1107px;
    height: 240px;
    background: linear-gradient(90deg, var(--navy) 0%, var(--navy-light) 70%, #3a2550 100%);
  }
  .contact {
    position: absolute;
    left: 800px;
    top: 52px;
    font-family: "Roboto", sans-serif;
    font-size: 23px;
    line-height: 28px;
    color: var(--white);
  }
  .contact-address { margin: 0 0 10px; }
  .contact-line {
    display: flex;
    align-items: center;
    gap: 7px;
    margin: 0 0 8px;
  }
  .contact-icon { width: 19px; height: 19px; flex: none; }
  .brand {
    position: absolute;
    left: 65px;
    top: 272px;
    display: flex;
    align-items: center;
    gap: 22px;
  }
  .brand-dot {
    width: 64px;
    height: 64px;
    border-radius: 50%;
    background: var(--navy);
  }
  .brand-name {
    font-family: "Mulish", sans-serif;
    font-weight: 700;
    font-size: 58px;
    color: var(--navy);
    letter-spacing: 0.5px;
  }
  .letter-body {
    position: absolute;
    left: 65px;
    top: 477px;
    width: 977px;
    font-size: 20.5px;
    line-height: 31.7px;
  }
  .recipient { margin: 0 0 22px; }
  .letter-body p.paragraph {
    margin: 0 0 32px;
    text-align: justify;
  }
  .letter-body p.paragraph.tight { margin-bottom: 20px; }
  .closing { margin: 20px 0 14px; }
  .signature {
    width: 200px;
    height: 80px;
    background: var(--placeholder);
  }
  .footer-band {
    position: absolute;
    left: 0;
    top: 1541px;
    width: 1107px;
    height: 23px;
    background: linear-gradient(90deg, var(--navy), var(--navy-light) 45%, var(--red-dark) 55%, var(--red));
  }
</style>
</head>
<body>
<div class="letterhead">
  <div class="header-band" role="img" aria-label="Decorative navy header band with red accent"></div>

  <div class="contact">
    <p class="contact-address">1475 Calloway Street<br>Suite 210, Houston,<br>Texas 77041</p>
    <p class="contact-line">
      <svg class="contact-icon" viewBox="0 0 20 20" aria-label="Phone"><path d="M2 8 C2 4 18 4 18 8 L15 9 L14 7 C11 6 9 6 6 7 L5 9 Z M5 10 H15 L17 16 H3 Z" fill="#fff"/></svg>
      <span>832-361-9027</span>
    </p>
    <p class="contact-line">
      <svg class="contact-icon" viewBox="0 0 20 20" aria-label="Fax"><rect x="5" y="2" width="10" height="5" fill="#fff"/><rect x="2" y="7" width="16" height="8" rx="1.5" fill="#fff"/><rect x="5" y="12" width="10" height="6" fill="#fff" stroke="#13244a" stroke-width="1"/></svg>
      <span>832-614-7359</span>
    </p>
  </div>

  <div class="brand">
    <div class="brand-dot"></div>
    <div class="brand-name">Marwick Law</div>
  </div>

  <div class="letter-body">
    <p class="recipient">Mr/s<br>First Name and Last Name<br>Company Name<br>Address</p>
    <p class="paragraph">Lorem Ipsum is simply dummy text of the printing and typesetting industry. Lorem Ipsum has been the industry's standard dummy text ever since the 1500s, when an unknown printer took a galley of type and scrambled it to make a type specimen book. It has survived not only five centuries, but also the leap into electronic typesetting, remaining essentially unchanged. It was popularised in the 1960s with the release of Typeset sheets containing Lorem Ipsum passages.</p>
    <p class="paragraph tight">he standard chunk of Lorem Ipsum used since the 1500s is reproduced below for those interested. Sec&shy;tions 1.10.32 and 1.10.33 from "de Finibus Bonorum et Malorum" by Varennius are also reproduced in their exact original form, accompanied by English versions from the 1914 translation by H. Pellman. Lorem ipsum dolor sit amet, consectetur adipiscing elit, sed do eiusmod tempor incididunt ut labore et dolore magna aliqua.</p>
    <p class="paragraph tight">It is a long established fact that a reader will be distracted by the readable content of a page when look&shy;ing at its layout. The point of using Lorem Ipsum is that it has a more-or-less normal distribution of letters, as opposed to using 'Content here, content here', making it look like readable English. Many desktop publishing packages and web page editors now .</p>
    <p class="closing">Your Sincerely,</p>
    <div class="signature" role="img" aria-label="Handwritten signature"></div>
  </div>

  <div class="footer-band" role="img" aria-label="Decorative navy and red footer band"></div>
</div>
</body>
</html>
```